Mental Health care Company in Washington DC

We are a new mental health care services provider in Washington DC. Please look at these sites.
https://brightwaterfamilysupport.com
https://www.quietharborinc.com
https://willowgate-dc.org/
https://www.tidepathdc.com
https://www.thelanternofdc.com

```html
<!DOCTYPE html>
<html lang="en">
<head>
<meta charset="utf-8">
<title>Lumen Health Services</title>
<link rel="stylesheet" href="https://fonts.googleapis.com/css2?family=Manrope:wght@400;500;600;700;800&display=swap">
<style>
:root{
  --teal:#7fd3d6;
  --teal-soft:#e4f6f7;
  --teal-mid:#a9e3e5;
  --teal-deep:#1bb3bb;
  --orange:#f7851f;
  --orange-deep:#f26a14;
  --navy:#0e2a47;
  --ink:#1d2430;
  --grey:#8a9099;
  --line:#e6ecef;
  --white:#fff;
  --red:#f04a4a;
}
*{box-sizing:border-box;margin:0;padding:0}
html,body{width:1200px;height:1200px;overflow:hidden;background:#fff}
body{font-family:'Manrope',sans-serif;color:var(--ink);position:relative}
.abs{position:absolute}
.photo{position:absolute;border-radius:2px}

/* wordmark: single name with a plain dot */
.wordmark{display:flex;align-items:center;font-weight:700;line-height:1;white-space:nowrap}
.wordmark .dot{border-radius:50%;background:var(--teal);flex:none}

/* ===== overview column ===== */
.ov{position:absolute;left:0;top:0;width:340px;height:1200px}
.ov .nav{position:absolute;top:10px;left:30px;right:14px;display:flex;align-items:center;font-size:4px;font-weight:600}
.ov .brand{font-size:8px;color:var(--navy);margin-right:22px;gap:3px}
.ov .brand .dot{width:5px;height:5px}
.ov .nav a{color:var(--orange);text-decoration:none;margin-right:9px}
.ov .nav a.on{color:var(--navy)}
.ov .nav .btn{margin-left:auto;background:var(--teal);color:#fff;padding:3px 8px;font-size:3.5px}
.ov-hero{left:17px;top:26px;width:309px;height:178px;background:linear-gradient(120deg,#d8f4f6,#b8ebee 60%,#e9f9fa)}
.ov-hero h1{position:absolute;left:19px;top:46px;font-size:15px;line-height:16px;font-weight:800;letter-spacing:-.5px;color:var(--teal)}
.ov-hero h1 .o{color:var(--orange)}
.ov-hero .covid{position:absolute;left:0;right:0;bottom:0;height:21px;background:var(--orange);color:#fff;font-size:4px;display:flex;align-items:center;justify-content:center;gap:14px}
.tiny{font-size:3.5px;color:var(--grey);line-height:6px}
.sb{font-size:4px;font-weight:700;color:#fff;background:var(--ink);padding:4px 7px;display:inline-block}
.card{position:absolute;background:#fff;box-shadow:0 2px 6px rgba(0,0,0,.06)}
.avatar{width:34px;height:34px;border-radius:50%;background:linear-gradient(160deg,#bfe8ea,#5cc4cb);margin:8px auto 4px}

/* ===== detail column ===== */
.dt{position:absolute;left:400px;top:0;width:800px;height:1200px}
.dt .nav{position:absolute;top:22px;left:43px;right:40px;height:30px;display:flex;align-items:center;font-size:11px;font-weight:600}
.dt .brand{font-size:22px;color:var(--navy);margin-right:60px;letter-spacing:-.5px;gap:8px}
.dt .brand .dot{width:12px;height:12px}
.dt .nav a{color:var(--orange);text-decoration:none;margin-right:22px}
.dt .nav a.on{color:var(--navy)}
.dt .nav .btn{margin-left:auto;margin-right:0;background:var(--teal);color:#fff;padding:10px 14px;font-size:9px}
.hero{left:11px;top:70px;width:749px;height:430px;border-radius:4px;overflow:hidden;background:#fff}
.hero .bg{position:absolute;left:0;top:0;right:0;height:335px;background:linear-gradient(115deg,#d6f3f5 0%,#b6eaee 45%,#e5f8f9 100%)}
.hero .eyebrow{position:absolute;left:45px;top:90px;font-size:11px;color:#9aa3a8}
.hero h1{position:absolute;left:45px;top:113px;font-size:39px;line-height:39px;font-weight:800;letter-spacing:-1.5px;color:var(--teal)}
.hero h1 .o{color:var(--orange)}
.hero .b1{position:absolute;left:45px;top:292px;width:90px;height:33px;background:var(--ink);color:#fff;font-size:9px;font-weight:600;display:flex;align-items:center;justify-content:center}
.hero .b2{position:absolute;left:144px;top:292px;width:89px;height:33px;border:1px solid #cfe9eb;color:var(--ink);font-size:9px;font-weight:600;display:flex;align-items:center;justify-content:center;gap:5px}
.hero .covid{position:absolute;left:0;right:0;top:380px;height:50px;background:var(--orange);color:#fff;font-size:10px;display:flex;align-items:center;justify-content:center}
.hero .covid b{font-weight:700;display:flex;align-items:center;gap:6px}
.hero .covid i{display:inline-block;width:1px;height:12px;background:rgba(255,255,255,.6);margin:0 16px}
.verified{position:absolute;right:0;top:217px;width:140px;height:60px;background:rgba(255,255,255,.85);display:flex;align-items:center;gap:10px;padding-left:14px}
.heart{position:absolute;border-radius:50%;background:var(--red);display:flex;align-items:center;justify-content:center}
.vert{position:absolute;left:-12px;top:145px;transform-origin:left top;transform:rotate(-90deg) translateX(-200px);font-size:8px;color:var(--ink);white-space:nowrap;font-weight:500}
.about-h{font-size:15.5px;line-height:30.5px;font-weight:800;letter-spacing:-.6px;color:var(--ink)}
.tag{display:flex;align-items:center;gap:10px;font-size:10px;color:var(--ink);font-weight:500}
.tag .ic{width:32px;height:32px;border-radius:50%;background:var(--teal-soft);display:flex;align-items:center;justify-content:center}
.svc{position:absolute;background:#fff;box-shadow:0 4px 14px rgba(0,0,0,.05)}
.svc .ic{width:60px;height:60px;border-radius:50%;background:var(--teal-soft);display:flex;align-items:center;justify-content:center;margin:29px 0 0 29px}
.svc h4{font-size:10.5px;line-height:16px;font-weight:700;margin:14px 0 0 29px;color:var(--ink)}
.svc p{font-size:9.5px;line-height:16.5px;color:var(--grey);margin:3px 0 0 29px}
.foot{position:absolute;left:17px;top:1147px;width:309px;height:33px;background:var(--navy);display:flex;align-items:center;padding-left:19px;font-size:3.5px;color:#fff;gap:10px}
.foot .wordmark{font-size:9px;color:#fff;margin-right:14px;gap:3px}
.foot .wordmark .dot{width:5px;height:5px}
</style>
</head>
<body>

<!-- ===== full page overview ===== -->
<section class="ov" aria-label="Full page overview">
  <div class="nav">
    <div class="wordmark brand"><span class="dot"></span>Lumen</div>
    <a class="on">Home</a><a>About</a><a>Treatments</a><a>Doctors</a><a>Timetable</a><a>Contact</a>
    <span class="btn">Make an Appointment</span>
  </div>
  <div class="abs" style="left:7px;font-size:2.5px;transform:rotate(-90deg);transform-origin:left top;top:140px;white-space:nowrap;color:#555">Arrange your appointment — Book appointment</div>

  <div class="abs ov-hero">
    <div class="photo" role="img" aria-label="Smiling female doctor in a white coat holding a brain model" style="left:160px;top:8px;width:149px;height:149px;background:linear-gradient(180deg,#c3ecef,#f4f7f8)"></div>
    <div class="tiny" style="position:absolute;left:19px;top:36px">Tell us your problem!</div>
    <h1>Most trusted<br><span class="o">Mental Health</span><br><span class="o">Care</span> partner<br>for your life.</h1>
    <div class="heart" style="left:142px;top:62px;width:17px;height:17px"><svg width="7" height="7" viewBox="0 0 24 24"><path fill="#fff" d="M12 21s-8-5.3-8-11a4.5 4.5 0 0 1 8-2.8A4.5 4.5 0 0 1 20 10c0 5.7-8 11-8 11z"/></svg></div>
    <div class="abs" style="left:253px;top:90px;width:56px;height:24px;background:rgba(255,255,255,.85);font-size:3.5px;padding:7px 0 0 17px">Verified doctors<br><span style="color:var(--grey)">Professional doctor</span></div>
    <span class="sb" style="position:absolute;left:19px;top:122px;font-size:3.5px">Find a doctor</span>
    <span style="position:absolute;left:60px;top:122px;font-size:3.5px;border:1px solid #cde8ea;padding:4px 7px">Video call</span>
    <div class="covid"><span>ⓘ Covid-19 information</span><span>Clean your hands frequently with alcohol-based hand soap and water.</span></div>
  </div>

  <!-- about -->
  <div class="photo" role="img" aria-label="Two doctors in a clinic" style="left:36px;top:240px;width:98px;height:123px;background:linear-gradient(160deg,#e8eaea,#c9d7db)"></div>
  <div class="photo" role="img" aria-label="Family outdoors, father carrying daughter" style="left:91px;top:274px;width:77px;height:100px;background:linear-gradient(160deg,#e9efe6,#a9b89a)"></div>
  <div class="abs" style="left:20px;top:302px;width:30px;height:30px;border-radius:50%;background:#fff;box-shadow:0 2px 5px rgba(0,0,0,.1)"></div>
  <div class="abs tiny" style="left:198px;top:230px;color:var(--ink)">About Lumen Health Services</div>
  <div class="abs" style="left:198px;top:249px;font-size:6.5px;font-weight:800;line-height:12.5px;letter-spacing:-.2px">Lumen Health emerged as an outpatient<br>behavioral health practice in<br>Washington, DC<br>in the year of 2014.</div>
  <div class="abs tiny" style="left:198px;top:303px">We value each and every human life placed in our hands<br>and constantly work towards meeting the expectations of<br>our customers and stake holders.</div>
  <div class="abs" style="left:198px;top:329px;font-size:13px;font-weight:800">722+</div>
  <div class="abs" style="left:229px;top:333px;width:23px;height:7px;background:var(--orange)"></div>
  <div class="abs tiny" style="left:266px;top:330px;color:var(--ink)">5 star reviews from<br>our satisfied people.</div>
  <div class="abs" style="left:198px;top:353px;width:39px;height:12px;background:var(--teal);color:#fff;font-size:3.5px;display:flex;align-items:center;justify-content:center">More about us</div>

  <!-- services -->
  <div class="abs" style="left:17px;top:391px;width:309px;height:177px;background:var(--teal-soft)"></div>
  <div class="abs tiny" style="left:36px;top:422px;color:var(--ink)">How we help you</div>
  <div class="abs" style="left:36px;top:440px;font-size:12px;font-weight:800;line-height:12px;letter-spacing:-.4px">Services we<br>offer</div>
  <div class="abs tiny" style="left:36px;top:468px">Each of the services we offer is tailored to our<br>client's needs. We aim to improve the lives<br>and help them reach their full potential.</div>
  <span class="sb abs" style="left:36px;top:498px;font-size:3.5px">All treatments</span>
  <div class="card" style="left:143px;top:416px;width:79px;height:95px;padding:44px 0 0 12px"><div style="font-size:4px;font-weight:700">Substance Abuse/<br>Addiction</div><div class="tiny">Lorem ipsum is simply dummy<br>typesetting.</div><div style="font-size:3.5px;margin-top:6px">⊕ Know more</div></div>
  <div class="card" style="left:229px;top:416px;width:79px;height:102px;padding:44px 0 0 11px"><div style="font-size:4px;font-weight:700">Psychiatric Consultations</div><div class="tiny">Lorem ipsum is simply dummy<br>text of simply printing<br>text of simply printing<br>typesetting.</div><div style="font-size:3.5px;margin-top:4px">⊕ Know more</div></div>
  <div class="card" style="left:315px;top:416px;width:11px;height:95px"></div>
  <div class="abs" style="left:50px;top:535px;font-size:12px;font-weight:700">4.98</div><div class="abs tiny" style="left:81px;top:536px;color:var(--ink)">★★★★★<br>2,488 rating.</div>
  <div class="abs" style="left:142px;top:535px;font-size:12px;font-weight:700">98<sup style="font-size:5px">%</sup></div><div class="abs tiny" style="left:168px;top:536px;color:var(--ink)">Genuine positive<br>feedback.</div>
  <div class="abs" style="left:234px;top:535px;font-size:12px;font-weight:700">200<sup style="font-size:5px">+</sup></div><div class="abs tiny" style="left:267px;top:536px;color:var(--ink)">Daily patients<br>consulted.</div>

  <!-- mission -->
  <div class="photo" role="img" aria-label="Patient consulting a doctor at a desk" style="left:36px;top:595px;width:132px;height:94px;background:linear-gradient(160deg,#d9cdbf,#5d6f86)"></div>
  <div class="abs" style="left:70px;top:637px;width:64px;height:12px;border-radius:6px;background:#fff;font-size:3.5px;display:flex;align-items:center;justify-content:center">▶ See our virtual tour</div>
  <div class="abs tiny" style="left:198px;top:597px;color:var(--ink)">Modern technologies</div>
  <div class="abs" style="left:198px;top:611px;font-size:12px;font-weight:800;line-height:12px;letter-spacing:-.3px">Our Mission<br>Statement</div>
  <div class="abs tiny" style="left:198px;top:642px">To provide quality mental health treatment and<br>services to eligible District of Columbia residents in an<br>environment that encourages them to become the<br>best and healthiest versions of themselves.</div>
  <div class="abs" style="left:198px;top:678px;width:46px;height:12px;background:var(--teal);color:#fff;font-size:3.5px;display:flex;align-items:center;justify-content:center">☏ +1 202 555 0147</div>
  <div class="abs tiny" style="left:113px;top:708px;color:var(--ink)"><span style="color:var(--orange)">☺</span> We can give you the big smile you've always wanted.</div>

  <!-- doctors -->
  <div class="abs" style="left:17px;top:750px;width:309px;height:272px;background:var(--teal-soft)"></div>
  <div class="abs" style="left:36px;top:733px;width:271px;height:37px;background:var(--teal);color:#fff;display:flex;align-items:center;font-size:3.5px;gap:20px;padding-left:17px">
    <span style="font-size:6px;font-weight:700;line-height:7px">Find the right<br>doctor for you.</span>
    <span>01 &nbsp; Search doctor</span><span>02 &nbsp; Book schedule</span><span>03 &nbsp; Make a payment</span>
  </div>
  <div class="abs" style="left:0;width:343px;top:789px;text-align:center;font-size:12px;font-weight:800">Qualified doctors</div>
  <div class="card" style="left:36px;top:815px;width:62px;height:90px;text-align:center;font-size:3.5px"><div class="avatar" role="img" aria-label="Doctor portrait"></div><b>Dr. Owen Marsh</b><div class="tiny">Specialize in psychiatry<br>at linden hospital.</div></div>
  <div class="card" style="left:105px;top:815px;width:62px;height:90px;text-align:center;font-size:3.5px"><div class="avatar" role="img" aria-label="Doctor portrait"></div><b>Dr. Elena Pryce</b><div class="tiny">Specialize in cancer at<br>linden hospital.</div></div>
  <div class="card" style="left:175px;top:815px;width:62px;height:90px;text-align:center;font-size:3.5px"><div class="avatar" role="img" aria-label="Doctor portrait"></div><b>Dr. Marcus Hale</b><div class="tiny">Specialize in pediatrics<br>at linden hospital.</div></div>
  <div class="card" style="left:245px;top:815px;width:62px;height:90px;text-align:center;font-size:3.5px"><div class="avatar" role="img" aria-label="Doctor portrait"></div><b>Dr. Nadia Cole</b><div class="tiny">Specialize in psychiatry<br>at linden hospital.</div></div>
  <div class="abs tiny" style="left:98px;top:920px;color:var(--ink)"><span style="background:var(--teal);color:#fff;padding:0 4px;border-radius:3px">TRUST</span> Genuine 10000+ people trusting Lumen hospital treatment.</div>
  <div class="abs" style="left:0;width:343px;top:953px;text-align:center;font-size:12px;font-weight:800">Our Partners</div>
  <div class="abs" style="left:52px;top:976px;width:30px;height:14px;background:#d6eef0"></div>
  <div class="abs" style="left:122px;top:976px;width:30px;height:14px;background:#d6eef0"></div>
  <div class="abs" style="left:191px;top:976px;width:30px;height:14px;background:#d6eef0"></div>
  <div class="abs" style="left:259px;top:976px;width:30px;height:14px;background:#d6eef0"></div>

  <!-- appointment -->
  <div class="abs" style="left:36px;top:1047px;font-size:12px;font-weight:800;line-height:12px;letter-spacing:-.3px">Request an<br>appointment.</div>
  <div class="abs tiny" style="left:36px;top:1076px">Location<br>1840 Larkspur Avenue SE<br>Washington, DC 20020</div>
  <div class="abs" style="left:36px;top:1112px;width:15px;height:15px;border-radius:50%;background:var(--teal)"></div>
  <div class="abs tiny" style="left:64px;top:1112px;color:var(--ink)">For urgent matters<br><b style="font-size:4.5px">+1 202 555 0147</b></div>
  <div class="abs tiny" style="left:128px;top:1047px;width:86px;height:13px;border:1px solid var(--line);padding:3px 6px">Patient's full name*</div>
  <div class="abs tiny" style="left:221px;top:1047px;width:86px;height:13px;border:1px solid var(--line);padding:3px 6px">Select doctor</div>
  <div class="abs tiny" style="left:128px;top:1066px;width:86px;height:13px;border:1px solid var(--line);padding:3px 6px">Patient's email*</div>
  <div class="abs tiny" style="left:221px;top:1066px;width:86px;height:33px;border:1px solid var(--line);padding:3px 6px">Your message</div>
  <div class="abs tiny" style="left:128px;top:1085px;width:86px;height:13px;border:1px solid var(--line);padding:3px 6px">01 / 01 / 2025</div>
  <div class="abs tiny" style="left:128px;top:1103px;font-size:2.8px;line-height:4.5px">We are committed to protecting your privacy. We will never<br>share your information without your explicit consent.</div>
  <div class="abs" style="left:261px;top:1105px;width:46px;height:13px;background:var(--teal);color:#fff;font-size:3.5px;display:flex;align-items:center;justify-content:center">Book appointment</div>

  <!-- footer -->
  <div class="foot">
    <div class="wordmark"><span class="dot"></span>Lumen</div>
    <span>Home</span><span>About</span><span>Treatments</span><span>Doctors</span><span>Timetable</span><span>Contact</span>
  </div>
  <div class="abs tiny" style="left:36px;top:1186px;font-size:2.8px">© 2025 <span style="color:var(--orange)">Lumen Health Services</span> - All rights reserved</div>
  <div class="abs tiny" style="left:244px;top:1186px;font-size:2.8px">Terms and conditions &nbsp;&nbsp;&nbsp;&nbsp; Privacy policy</div>
</section>

<!-- ===== detail view ===== -->
<section class="dt" aria-label="Home page detail">
  <div class="nav">
    <div class="wordmark brand"><span class="dot"></span>Lumen</div>
    <a class="on">Home</a><a>About</a><a>Treatments</a><a>Doctors</a><a>Timetable</a><a>Contact</a>
    <span class="btn">▣ Make an Appointment</span>
  </div>
  <div class="vert">☒ &nbsp;Arrange your appointment — <b>Book appointment</b></div>

  <div class="abs hero">
    <div class="bg"></div>
    <div class="photo" role="img" aria-label="Smiling female doctor in a white coat and stethoscope holding a brain model" style="left:330px;top:20px;width:419px;height:360px;background:linear-gradient(180deg,rgba(255,255,255,0) 0%,rgba(240,246,247,.9) 60%,#f5f7f8 100%),linear-gradient(90deg,#bdebee,#d9e8ea)"></div>
    <div class="eyebrow">Tell us your problem!</div>
    <h1>Most trusted<br><span class="o">Mental Health</span><br><span class="o">Care</span> partner<br>for your life.</h1>
    <div class="heart" style="left:345px;top:146px;width:44px;height:44px"><svg width="16" height="16" viewBox="0 0 24 24"><path fill="#fff" d="M12 21s-8-5.3-8-11a4.5 4.5 0 0 1 8-2.8A4.5 4.5 0 0 1 20 10c0 5.7-8 11-8 11z"/></svg></div>
    <div class="verified">
      <svg width="22" height="26" viewBox="0 0 22 26"><path d="M11 1 21 5v7c0 7-5 11-10 13C6 23 1 19 1 12V5z" fill="var(--teal-deep)"/><circle cx="11" cy="13" r="5" fill="#fff"/><path d="m8.5 13 2 2 3.5-3.5" stroke="var(--teal-deep)" stroke-width="1.6" fill="none"/></svg>
      <div style="font-size:10px;font-weight:600;line-height:17px">Verified doctors<br><span style="font-weight:400;color:var(--grey);font-size:9px">Professional doctor</span></div>
    </div>
    <div class="b1">Find a doctor</div>
    <div class="b2"><svg width="10" height="8" viewBox="0 0 10 8"><rect x=".5" y=".5" width="6" height="7" fill="none" stroke="#1d2430"/><path d="M7 3l2.5-1.5v5L7 5z" fill="none" stroke="#1d2430"/></svg>Video call</div>
    <div class="covid"><b><svg width="15" height="15" viewBox="0 0 16 16"><circle cx="8" cy="8" r="7" fill="none" stroke="#fff" stroke-width="1.2"/><path d="M8 7v5M8 4.5v.5" stroke="#fff" stroke-width="1.4"/></svg>Covid-19 information</b><i></i>Clean your hands frequently with alcohol-based hand soap and water.</div>
  </div>

  <!-- about -->
  <div class="photo" role="img" aria-label="Two smiling doctors standing in a bright clinic" style="left:56px;top:587px;width:241px;height:300px;background:linear-gradient(160deg,#ecedee,#d0d9dd 60%,#b7c4c9)"></div>
  <div class="photo" role="img" aria-label="Father carrying his daughter on his shoulders outdoors" style="left:192px;top:672px;width:186px;height:240px;background:linear-gradient(170deg,#eef2ec,#c5cfb3 55%,#8c9a7c)"></div>
  <div class="abs" style="left:18px;top:737px;width:76px;height:76px;border-radius:50%;background:#fff;box-shadow:0 4px 14px rgba(0,0,0,.1)"></div>

  <div class="abs tag" style="left:450px;top:561px"><span class="ic"><svg width="12" height="12" viewBox="0 0 12 12"><rect x="1" y="1" width="10" height="10" fill="none" stroke="var(--teal-deep)"/><path d="M4 1v10M6 4h3M6 6h3M6 8h3" stroke="var(--teal-deep)" stroke-width=".8"/></svg></span>About Lumen Health Services</div>
  <div class="abs about-h" style="left:450px;top:606px">Lumen Health emerged as an outpatient<br>behavioral health practice in<br>Washington, DC<br>in the year of 2014.</div>
  <div class="abs" style="left:450px;top:740px;font-size:9.5px;line-height:16.5px;color:var(--grey)">We value each and every human life placed in our hands<br>and constantly work towards meeting the expectations of<br>our customers and stake holders.</div>
  <div class="abs" style="left:450px;top:803px;font-size:31px;font-weight:800;letter-spacing:-1px">722+</div>
  <div class="abs" style="left:524px;top:812px;width:58px;height:18px;background:var(--orange);color:#fff;font-size:9px;display:flex;align-items:center;justify-content:center;letter-spacing:1px">★★★★★</div>
  <div class="abs" style="left:598px;top:808px;width:1px;height:27px;background:var(--ink)"></div>
  <div class="abs" style="left:614px;top:808px;font-size:9.5px;line-height:13.5px">5 star reviews from<br>our satisfied people.</div>
  <div class="abs" style="left:451px;top:860px;width:93px;height:31px;background:var(--teal);color:#fff;font-size:9px;font-weight:600;display:flex;align-items:center;justify-content:center">More about us</div>

  <!-- services -->
  <div class="abs" style="left:11px;top:954px;width:749px;height:246px;background:var(--teal-soft)"></div>
  <div class="abs tag" style="left:56px;top:1025px;font-size:10.5px"><span class="ic"><svg width="13" height="14" viewBox="0 0 22 26"><path d="M11 1 21 5v7c0 7-5 11-10 13C6 23 1 19 1 12V5z" fill="none" stroke="var(--teal-deep)" stroke-width="2"/><path d="m7 13 3 3 5-5" stroke="var(--teal-deep)" stroke-width="2" fill="none"/></svg></span>How we help you</div>
  <div class="abs" style="left:56px;top:1068px;font-size:31px;line-height:30px;font-weight:800;letter-spacing:-1px">Services we<br>offer</div>
  <div class="abs" style="left:56px;top:1140px;font-size:9.5px;line-height:16.5px;color:var(--grey)">Each of the services we offer is tailored to our<br>client's needs. We aim to improve the lives<br>and help them reach their full potential.</div>
  <div class="svc" style="left:316px;top:1014px;width:197px;height:186px">
    <div class="ic"><svg width="26" height="26" viewBox="0 0 26 26"><path d="M11 3h4v4h4v4h-4v4h-4v-4H7V7h4z" fill="var(--orange)"/><path d="M2 20c4-3 7-3 10-1h5c2 0 2 3 0 3h-5M9 24c4 0 9 0 15-5" stroke="var(--orange)" stroke-width="2" fill="none"/></svg></div>
    <h4>Substance Abuse/<br>Addiction</h4>
    <p>Lorem ipsum is simply dummy<br>typesetting.</p>
  </div>
  <div class="svc" style="left:523px;top:1014px;width:190px;height:186px">
    <div class="ic"><svg width="26" height="26" viewBox="0 0 26 26"><path d="M13 3a9 9 0 0 0-9 9l-2 4h3v4c0 2 1 3 3 3h3v3h9v-7a9 9 0 0 0-7-16z" fill="var(--orange)"/><circle cx="13" cy="11" r="3" fill="#fff"/></svg></div>
    <h4>Psychiatric Consultations</h4>
    <p>Lorem ipsum is simply dummy<br>text of simply printing<br>text of simply printing<br>typesetting.</p>
  </div>
  <div class="svc" style="left:731px;top:1014px;width:29px;height:186px"></div>
</section>

</body>
</html>
```